Professional Photography Business cards

I need business cards that include my logo which I have uploaded. I run a photography business. I am open to ideas but I would like one side to have my logo and the other side to have my contact info. I don't have a website made but I do own a website domain. I have uploaded 2 different logo color schemes. My business colors are Blue, black , and white.

Business Name
Business Phone Number
Business Email
Business Website address
Instagram

Industry/Entity Type

Professional Photography

Contact Information for Business Card

Phone Number: 916-384-7702 email: info@tlane-studio.example Instagram: @t.lanestudio website doman- www.tlane-studio.example

Requirements
Must have
• I like the idea of a business card with a full black background front and back of card. My colors must include royal blue, black, and white

```html
<!DOCTYPE html>
<html lang="en">
<head>
<meta charset="utf-8">
<title>Tessa Lane Photography – Business Cards</title>
<link rel="stylesheet" href="https://fonts.googleapis.com/css2?family=Montserrat:wght@300;400;500;700&display=swap">
<style>
  :root {
    --page-bg: #05070d;
    --card-bg: #0c1120;
    --card-edge: #1a2136;
    --gold: #d4a93a;
  }
  * { margin: 0; padding: 0; box-sizing: border-box; }
  html, body {
    width: 1200px;
    height: 800px;
    overflow: hidden;
    background: var(--page-bg);
    font-family: "Montserrat", Arial, sans-serif;
  }
  .sheet {
    position: relative;
    width: 1200px;
    height: 800px;
    display: flex;
    align-items: center;
    justify-content: center;
    gap: 48px;
  }
  .card {
    position: relative;
    width: 532px;
    height: 304px;
    background: radial-gradient(ellipse at 60% 40%, #121a2e 0%, var(--card-bg) 70%);
    border: 1px solid var(--card-edge);
    border-radius: 4px;
    box-shadow: 0 18px 40px rgba(0,0,0,0.6);
    color: var(--gold);
    overflow: hidden;
  }

  /* Contact side */
  .card-contact .holder {
    position: absolute;
    left: 38px;
    top: 66px;
  }
  .holder-name {
    font-size: 22px;
    letter-spacing: 0.5px;
    line-height: 1;
    white-space: nowrap;
  }
  .holder-name .first { font-weight: 700; }
  .holder-name .last { font-weight: 300; }
  .holder-role {
    margin-top: 6px;
    font-size: 12.5px;
    font-weight: 400;
    letter-spacing: 0.6px;
  }
  .card-contact .brand {
    position: absolute;
    right: 36px;
    top: 52px;
    text-align: right;
  }
  .card-contact .brand-name {
    font-size: 17px;
    letter-spacing: 3px;
    line-height: 1.35;
  }
  .contact-list {
    position: absolute;
    left: 38px;
    bottom: 38px;
    list-style: none;
    font-size: 12.5px;
    font-weight: 400;
    letter-spacing: 0.5px;
    line-height: 1.6;
  }

  /* Brand name set in type */
  .brand-name {
    display: block;
    font-weight: 500;
    color: var(--gold);
    white-space: nowrap;
  }
  .brand-line {
    display: flex;
    align-items: center;
    gap: 12px;
  }
  .brand-dot {
    flex: none;
    border: 2px solid var(--gold);
    border-radius: 50%;
  }

  /* Logo side */
  .card-logo .brand {
    position: absolute;
    left: 0;
    right: 0;
    top: 112px;
    display: flex;
    justify-content: center;
  }
  .card-logo .brand-name {
    font-size: 28px;
    letter-spacing: 4px;
  }
  .card-logo .brand-dot {
    width: 18px;
    height: 18px;
  }
  .card-logo .web {
    position: absolute;
    left: 0;
    right: 0;
    bottom: 36px;
    text-align: center;
    font-size: 13px;
    font-weight: 400;
    letter-spacing: 0.6px;
  }
</style>
</head>
<body>
  <main class="sheet">
    <section class="card card-contact" aria-label="Business card, contact side">
      <div class="holder">
        <p class="holder-name"><span class="first">TESSA</span> <span class="last">LANE</span></p>
        <p class="holder-role">OWNER/PHOTOGRAPHER</p>
      </div>
      <div class="brand">
        <span class="brand-name">T. LANE<br>PHOTOGRAPHY</span>
      </div>
      <ul class="contact-list">
        <li class="contact-phone">916-384-7702</li>
        <li class="contact-email">info@tlane-studio.example</li>
        <li class="contact-web">www.tlane-studio.example</li>
        <li class="contact-social">@t.lanestudio</li>
      </ul>
    </section>

    <section class="card card-logo" aria-label="Business card, logo side">
      <div class="brand">
        <div class="brand-line">
          <span class="brand-name">T. LANE PHOTOGRAPHY</span>
          <span class="brand-dot"></span>
        </div>
      </div>
      <p class="web">www.tlane-studio.example</p>
    </section>
  </main>
</body>
</html>
```